Hvac and insulation company needs good looking business card design

We are hvac and insulation company and looking for a new business cards that look to today standards designs

Target Market(s)

homeowners

Industry/Entity Type

Hvac

Contact Information for Business Card

Name: Walter Brinoku
Home comfort consultant
address: 4827 Dunmore St #215 Oakland, CA 94619
office: 888-316-2790
cell: 510-742-3185
Lic.# 584261
Email: walter@corvane-hvac.com
Web: corvane-hvac.com

Requirements
Must have
• clean and sleek look
Nice to have
• simple with a clean look
Should not have
• to busy business card

```html
<!DOCTYPE html>
<html lang="en">
<head>
<meta charset="UTF-8">
<title>Corvane Home Solutions – Business Card</title>
<link rel="stylesheet" href="https://fonts.googleapis.com/css2?family=Arimo:wght@400;700&display=swap">
<style>
  :root {
    --brand-orange: #f28421;
    --brand-peach: #fde6d6;
    --card-white: #ffffff;
    --ink: #2b2b2b;
    --muted: #7a7a7a;
    --backdrop: #ecebe8;
  }
  * { box-sizing: border-box; margin: 0; padding: 0; }
  html, body {
    width: 1200px; height: 900px; overflow: hidden;
    background: var(--backdrop);
    font-family: "Arimo", Arial, sans-serif;
  }
  .stage {
    position: relative; width: 1200px; height: 900px;
    display: flex; flex-direction: column; align-items: center; justify-content: center; gap: 50px;
  }
  .card {
    position: relative; width: 560px; height: 320px; overflow: hidden;
    box-shadow: 0 6px 18px rgba(0,0,0,.14);
  }

  /* Back side */
  .card--back { background: var(--brand-orange); color: var(--card-white); }
  .card--back .wordmark {
    position: absolute; left: 0; right: 0; top: 118px;
    display: flex; justify-content: center; align-items: center; gap: 14px;
  }
  .card--back .wordmark-dot { width: 22px; height: 22px; border-radius: 50%; background: var(--card-white); }
  .card--back .wordmark-name { font-weight: 700; font-size: 38px; letter-spacing: .5px; color: var(--card-white); }
  .card--back .address {
    position: absolute; left: 0; right: 0; bottom: 36px;
    text-align: center; font-size: 15px; letter-spacing: .2px;
  }

  /* Front side */
  .card--front { background: var(--card-white); color: var(--ink); }
  .card--front .bands { position: absolute; inset: 0; }
  .card--front .wordmark {
    position: absolute; left: 40px; top: 62px;
    display: flex; align-items: center; gap: 12px;
  }
  .card--front .wordmark-dot { width: 20px; height: 20px; border-radius: 50%; background: var(--brand-orange); }
  .card--front .wordmark-name { font-weight: 700; font-size: 30px; color: var(--brand-orange); }
  .contact-block { position: absolute; left: 72px; top: 126px; }
  .person-name { font-weight: 700; font-size: 22px; color: var(--brand-orange); }
  .person-title { font-size: 14px; color: var(--ink); margin-top: 3px; }
  .licence { font-size: 14px; margin-top: 14px; }
  .licence-label { color: var(--brand-orange); }
  .contact-list { list-style: none; margin-top: 6px; }
  .contact-list li {
    display: flex; align-items: center; gap: 8px;
    font-size: 14px; line-height: 20px; color: var(--ink);
  }
  .contact-list li.office { padding-left: 0; }
  .contact-icon { width: 12px; height: 12px; flex: none; fill: var(--brand-orange); }
  .icon-spacer { width: 12px; height: 12px; flex: none; }
</style>
</head>
<body>
<main class="stage">

  <section class="card card--back" aria-label="Card back">
    <div class="wordmark">
      <span class="wordmark-dot"></span>
      <span class="wordmark-name">Corvane Home Solutions</span>
    </div>
    <p class="address">4827 Dunmore St #215 Oakland, CA 94619</p>
  </section>

  <section class="card card--front" aria-label="Card front">
    <svg class="bands" width="560" height="320" viewBox="0 0 560 320" aria-hidden="true">
      <polygon points="300,0 560,0 560,58 340,58" fill="var(--brand-peach)"/>
      <polygon points="430,120 560,102 560,320 470,320" fill="var(--brand-peach)"/>
    </svg>

    <div class="wordmark">
      <span class="wordmark-dot"></span>
      <span class="wordmark-name">Corvane Home Solutions</span>
    </div>

    <div class="contact-block">
      <p class="person-name">Walter Brinoku</p>
      <p class="person-title">Home Comfort Consultant</p>
      <p class="licence"><span class="licence-label">LIC.</span># 584261</p>
      <ul class="contact-list">
        <li class="office"><span class="icon-spacer"></span>888-316-2790</li>
        <li>
          <svg class="contact-icon" viewBox="0 0 12 12" aria-label="Phone"><path d="M2 1h2l1 3-1.5 1a6 6 0 0 0 3.5 3.5L8 7l3 1v2a1 1 0 0 1-1 1A9 9 0 0 1 1 2a1 1 0 0 1 1-1z"/></svg>
          510-742-3185
        </li>
        <li>
          <svg class="contact-icon" viewBox="0 0 12 12" aria-label="Email"><path d="M0 2h12v8H0z M0 2l6 4 6-4" fill="var(--brand-orange)"/><path d="M0.5 2.5l5.5 4 5.5-4" stroke="#fff" stroke-width="1" fill="none"/></svg>
          walter@corvane-hvac.com
        </li>
        <li>
          <svg class="contact-icon" viewBox="0 0 12 12" aria-label="Website"><circle cx="6" cy="6" r="5.5"/><path d="M6 .5v11M.5 6h11M6 .5c-3 3-3 8 0 11M6 .5c3 3 3 8 0 11" stroke="#fff" stroke-width=".8" fill="none"/></svg>
          www.corvane-hvac.com
        </li>
      </ul>
    </div>
  </section>

</main>
</body>
</html>
```